LM-Steuerberatung WordPress Site fully implemented (tax advisor)

Hello!
I need a little Wordpress Site for my newly founded Tax-Advisor Company.
I am a one-man Office advising in the area of Crypto-Currency.
PLEASE only provide a Design, if you can also Implement a WP-Site afterwards on an existing Webspace.

Please find the Content and Website-Description in the attached Document

Language for the Website is German (for now)

Target Market(s)

Tax-Advisory (specialized in Crypto Currency)

Coding

Coded - Design and coding required

Number of Pages Required

5+ page

Font styles to use
Sans Serif

Requirements
Must have
• Wordpress Implementation afterwards - Details according to attached Project Information Document

```html
<!DOCTYPE html>
<html lang="de">
<head>
<meta charset="utf-8">
<title>Über mich – LM-Steuerberatung</title>
<link rel="stylesheet" href="https://fonts.googleapis.com/css2?family=Manrope:wght@400;500;600;700;800&display=swap">
<style>
:root{
  --navy:#1b2940;
  --navy-deep:#17223a;
  --text:#4a4f5a;
  --ink:#222a36;
  --white:#ffffff;
  --line:#3a4a66;
  --accent:#2f5db3;
}
*{margin:0;padding:0;box-sizing:border-box}
html,body{width:822px;height:1200px;overflow:hidden;background:var(--white)}
body{position:relative;font-family:'Manrope',sans-serif;color:var(--text)}
.abs{position:absolute}

.topbar{left:0;top:0;width:822px;height:35px;background:var(--navy)}
.social{display:flex;gap:14px;align-items:center}
.social span{display:block;width:9px;height:9px;border-radius:50%;background:var(--white)}
.topbar .social{left:69px;top:13px}
.topbar .contact{right:69px;top:10px;display:flex;gap:13px;color:var(--white);font-size:11px}
.contact svg{vertical-align:-2px;margin-right:3px}

.header{left:0;top:35px;width:822px;height:62px;background:var(--white)}
.brand{display:flex;align-items:center;gap:7px;font-weight:800;letter-spacing:.3px}
.brand i{display:block;width:22px;height:22px;background:var(--navy)}
.header .brand{left:69px;top:20px;font-size:13px;color:var(--navy)}
.nav{left:368px;top:23px;display:flex;gap:30px;font-size:11px;color:var(--ink);font-weight:500}
.nav .active{position:relative}
.nav .active::after{content:"";position:absolute;left:50%;top:19px;width:4px;height:4px;margin-left:-2px;border-radius:50%;background:var(--navy)}
.btn-kontakt{left:668px;top:16px;width:87px;height:30px;background:var(--navy);color:var(--white);border-radius:14px 4px 14px 4px;font-size:11.5px;font-weight:600;display:flex;align-items:center;justify-content:center}

.hero{left:0;top:97px;width:822px;height:158px;background:linear-gradient(100deg,#3b3d42 0%,#2a2b2f 35%,#6b5440 55%,#3a3838 75%,#5a5a5a 100%)}
.hero::after{content:"";position:absolute;inset:0;background:rgba(10,14,22,.55)}
.hero h1{position:absolute;z-index:1;left:0;right:0;top:62px;text-align:center;color:var(--white);font-size:28px;font-weight:700}

.portrait-frame{left:78px;top:296px;width:211px;height:229px;border:1px solid var(--navy);border-radius:14px}
.portrait{left:69px;top:300px;width:216px;height:231px;border-radius:14px;background:linear-gradient(180deg,#c9cacc 0%,#b7b8ba 45%,#2a2b2e 46%,#1c1d20 100%)}
.portrait-name{left:69px;top:541px;width:216px;text-align:center;font-size:15px;font-weight:700;color:var(--ink)}

.bio{left:305px;top:304px;width:452px;font-size:11.2px;line-height:18.8px}
.bio p{margin-bottom:6px}

.card{width:336px;height:183px;top:626px;border:1px solid var(--navy);border-radius:16px;padding:29px 13px 0 14px;font-size:11.2px;line-height:18.8px}
.card p{margin-bottom:5px}
.card b{color:var(--ink);font-weight:700}
.card-left{left:67px}
.card-right{left:420px}
.tab{top:610px;height:31px;border:1px solid var(--navy);border-radius:15px;background:var(--white);color:var(--navy);font-size:11px;font-weight:600;display:flex;align-items:center;justify-content:center}
.tab-left{left:165px;width:140px}
.tab-right{left:503px;width:169px}

.btn-profile{left:73px;top:849px;width:222px;height:35px;background:var(--navy);color:var(--white);border-radius:18px 4px 18px 4px;font-size:12px;font-weight:600;display:flex;align-items:center;justify-content:center;gap:4px}

.footer{left:0;top:937px;width:822px;height:263px;background:var(--navy-deep);color:var(--white)}
.footer .brand{left:67px;top:45px;font-size:15px;color:var(--white)}
.footer .brand i{width:26px;height:34px;background:var(--white)}
.f-about{left:68px;top:97px;width:220px;font-size:11.2px;line-height:17.6px}
.footer .social{left:69px;top:168px;gap:20px}
.footer .social span{width:11px;height:11px}
.divider{top:53px;width:1px;height:141px;background:var(--line)}
.divider::before{content:"";position:absolute;left:-3px;top:23px;width:3px;height:15px;background:var(--accent)}
.f-head{font-size:11.5px;font-weight:700}
.f-links{left:420px;top:55px;font-size:11.2px}
.f-links ul{list-style:none;margin-top:12px}
.f-links li{height:26.5px}
.f-contact{left:621px;top:55px;font-size:11.2px}
.f-contact div{margin-top:12px;height:26.5px;display:flex;align-items:center;gap:8px}
.rule{left:67px;top:221px;width:688px;height:1px;background:var(--line)}
.copy{left:0;right:0;top:236px;text-align:center;font-size:9.8px}
.copy b{font-weight:700}
</style>
</head>
<body>

<div class="abs topbar">
  <div class="abs social"><span></span><span></span><span></span></div>
  <div class="abs contact">
    <span><svg width="10" height="10" viewBox="0 0 24 24" fill="#fff"><path d="M6.6 10.8a15 15 0 0 0 6.6 6.6l2.2-2.2c.3-.3.7-.4 1-.2 1.1.4 2.3.6 3.6.6.6 0 1 .4 1 1V20c0 .6-.4 1-1 1A17 17 0 0 1 3 4c0-.6.4-1 1-1h3.5c.6 0 1 .4 1 1 0 1.3.2 2.5.6 3.6.1.3 0 .7-.2 1z"/></svg>+43 512 000 481</span>
    <span><svg width="11" height="9" viewBox="0 0 24 18" fill="#fff"><path d="M0 0h24v2L12 10 0 2z M0 4l12 8 12-8v14H0z"/></svg>office@lm-steuer.example</span>
  </div>
</div>

<header class="abs header">
  <div class="abs brand"><i></i>LM STEUERBERATUNG</div>
  <nav class="abs nav"><span>Home</span><span>Leistungen</span><span class="active">Über mich</span><span>Impressum</span></nav>
  <div class="abs btn-kontakt">Kontakt</div>
</header>

<section class="abs hero" role="img" aria-label="Dunkles Foto: Hand hält eine Münze neben einem Laptop"><h1>ÜBER MICH</h1></section>

<div class="abs portrait-frame"></div>
<div class="abs portrait" role="img" aria-label="Porträtfoto des Steuerberaters im dunklen Anzug"></div>
<div class="abs portrait-name">Mag. Lukas Moser</div>

<div class="abs bio">
  <p>Mag. Lukas Moser Ich blicke auf eine sehr umfassende Ausbildung und langjährige Berufserfahrung in der IT Branche zurück. Nach Abschluss des Wirtschaftsstudiums habe ich den klassischen Weg der</p>
  <p>Steuerberaterausbildung absolviert und bin in diesem Bereich seit über 13 Jahren beratend tätig.</p>
  <p>Durch die Kombination meines umfassenden Wissens in der IT und der Wirtschaft habe ich schon immer gerne Unternehmen mit besonderes technischen oder digitalen Geschäftsmodellen beraten. Seit mehreren Jahren bin ich privat an der</p>
  <p>Blockchaintechnologie und dem Krypto-Universum interessiert und bereits seit dem Jahre 2017 ist dieses Thema auch Teil meiner fixen Beratungsfelder in der Steuerberatung.</p>
</div>

<div class="abs card card-left">
  <p><b>2002</b> – HTL - Matura mit Schwerpunkt IT und Betrieblicher Organisation</p>
  <p><b>2009</b> –Studium BWL mit Schwerpunkten Banking &amp; Finance sowie Kapitalmärkte</p>
  <p><b>2012</b> – Buchhalter &amp; Bilanzbuchhalterprüfung</p>
  <p><b>2013</b> – Angelobung zum Steuerberater</p>
</div>
<div class="abs tab tab-left">AUSBILDUNG</div>

<div class="abs card card-right">
  <p><b>2003 - 2009</b> – Selbständig tätig im IT Sektor</p>
  <p><b>Seit 2009</b> – Beratend tätig in der Steuerberatung / Wirtschaftsprüfung in verschiedenen Kanzleien. Zuletzt in leitender Funktion bei Kanzlei Berger Tirol</p>
  <p><b>2022</b>: Gründung der eigenen Kanzlei LM-Steuerberatung mit Fokus Krypto-Beratung.</p>
</div>
<div class="abs tab tab-right">BERUFLICHER WERDEGANG</div>

<div class="abs btn-profile">Go to ProNetz Profile Profile
  <svg width="10" height="10" viewBox="0 0 20 20"><circle cx="10" cy="10" r="10" fill="#fff"/><path d="M8 5l5 5-5 5" stroke="#1b2940" stroke-width="2.5" fill="none"/></svg>
</div>

<footer class="abs footer">
  <div class="abs brand"><i></i>LM STEUERBERATUNG</div>
  <p class="abs f-about">Ihrem Spezialisten bei allen steuerlichen Themen rund um Einkünfte &amp; Vermögen aus Krypto-Assets.</p>
  <div class="abs social"><span></span><span></span><span></span></div>
  <div class="abs divider" style="left:352px"></div>
  <div class="abs divider" style="left:562px"></div>
  <div class="abs f-links">
    <div class="f-head">QUICK LINKS</div>
    <ul><li>Home</li><li>Leistungen</li><li>Über mich</li><li>Impressum</li><li>Kontakt</li></ul>
  </div>
  <div class="abs f-contact">
    <div class="f-head" style="margin-top:0;height:auto">CONTACT US</div>
    <div><svg width="12" height="9" viewBox="0 0 24 18" fill="#c8ccd4"><path d="M0 0h24v2L12 10 0 2z M0 4l12 8 12-8v14H0z"/></svg>office@lm-steuer.example</div>
    <div style="margin-top:0"><svg width="11" height="11" viewBox="0 0 24 24" fill="#c8ccd4"><path d="M6.6 10.8a15 15 0 0 0 6.6 6.6l2.2-2.2c.3-.3.7-.4 1-.2 1.1.4 2.3.6 3.6.6.6 0 1 .4 1 1V20c0 .6-.4 1-1 1A17 17 0 0 1 3 4c0-.6.4-1 1-1h3.5c.6 0 1 .4 1 1 0 1.3.2 2.5.6 3.6.1.3 0 .7-.2 1z"/></svg>+43 512 000 481</div>
  </div>
  <div class="abs rule"></div>
  <div class="abs copy">© 2022 <b>LM-Steuerberatung</b>. All right reserved</div>
</footer>

</body>
</html>
```